New Business Card Design Project LORVANTI-Italy

we are LORVANTI-Italy
our company in the market for 3 years we are luxury cosmetic company and its about time for a facelift :)
i will like to have elegant luxurious and unique business card
that will give the person that get it a unique, luxurious and elegant impression
I'm VERY OPEN FOR NEW IDEAS , even duo i add a few files of things that i see on line and i like them

i add my logo as well
my website is LORVANTI.COM
(if you would like to see the main style that we have)

Target Market(s)

adult that have money :)

Industry/Entity Type

Business

Contact Information for Business Card

Name - Dario Lorvanti
Position - CEO and CO Founder
address - 4817 E Halvern
telephone - 555-384-1926
email - dario@lorvanti.com
fax - 555-384-1926
website - LORVANTI.COM

Colors
000000
959595
fbee3e
ffffff

Requirements
Must have
• big logo in GOLD color
• elegant look
• impressive
Nice to have
• not must but maybe classy pattern background
• not must but maybe emblem
• maybe clear plastic business card
Should not have
• colors
• images

```html
<!DOCTYPE html>
<html lang="en">
<head>
<meta charset="utf-8">
<title>LORVANTI-Italy Business Card</title>
<link href="https://fonts.googleapis.com/css2?family=PT+Sans:wght@400;700&display=swap" rel="stylesheet">
<style>
  :root {
    --backdrop: #2b2724;
    --card-black: #121213;
    --card-edge: #1c1c1e;
    --gold: #d9ad3c;
    --gold-soft: #b8902e;
    --grey: #959595;
    --white: #ffffff;
  }
  * { box-sizing: border-box; margin: 0; padding: 0; }
  html, body {
    width: 1200px;
    height: 864px;
    overflow: hidden;
    background: var(--backdrop);
    font-family: "PT Sans", Arial, sans-serif;
  }
  .canvas {
    position: relative;
    width: 1200px;
    height: 864px;
  }
  .card {
    position: absolute;
    width: 560px;
    height: 320px;
    background: var(--card-black);
    border: 1px solid var(--card-edge);
    box-shadow: 0 18px 40px rgba(0,0,0,0.45);
  }
  /* Front */
  .card-front { left: 60px; top: 70px; }
  .brand-block {
    position: absolute;
    left: 0; right: 0; top: 62px;
    display: flex;
    flex-direction: column;
    align-items: center;
  }
  .brand-circle {
    width: 78px; height: 78px;
    border: 3px solid var(--gold);
    border-radius: 50%;
    margin-bottom: 22px;
  }
  .brand-name {
    color: var(--gold);
    font-weight: 400;
    font-size: 34px;
    letter-spacing: 3px;
  }
  .brand-rule {
    width: 230px;
    height: 2px;
    background: var(--gold);
    margin-top: 10px;
  }
  .front-web {
    position: absolute;
    left: 0; right: 0; bottom: 40px;
    text-align: center;
    color: var(--grey);
    font-size: 15px;
    letter-spacing: 4px;
  }
  /* Back */
  .card-back { left: 580px; top: 440px; }
  .back-mark {
    position: absolute;
    left: 40px; top: 70px;
    width: 180px; height: 180px;
    border: 4px solid var(--gold);
    border-radius: 50%;
    display: flex;
    align-items: center;
    justify-content: center;
  }
  .back-mark-name {
    color: var(--gold);
    font-size: 24px;
    font-weight: 400;
    letter-spacing: 2px;
  }
  .divider {
    position: absolute;
    left: 262px; top: 60px;
    width: 2px; height: 200px;
    background: linear-gradient(to bottom, rgba(255,255,255,0), rgba(255,255,255,0.85) 30%, rgba(255,255,255,0.85) 70%, rgba(255,255,255,0));
  }
  .contact {
    position: absolute;
    left: 286px; top: 72px;
    color: var(--white);
  }
  .contact-name {
    color: var(--gold);
    font-weight: 700;
    font-size: 21px;
    line-height: 1.1;
  }
  .contact-title {
    font-size: 18px;
    margin-bottom: 14px;
  }
  .contact-address {
    font-size: 14px;
    margin-bottom: 4px;
  }
  .contact-list { list-style: none; }
  .contact-list li {
    display: flex;
    align-items: center;
    gap: 8px;
    font-size: 14.5px;
    line-height: 20px;
  }
  .contact-list svg { width: 12px; height: 12px; fill: var(--gold); flex: none; }
</style>
</head>
<body>
<main class="canvas">
  <section class="card card-front" aria-label="Card front">
    <div class="brand-block">
      <div class="brand-circle"></div>
      <div class="brand-name">LORVANTI-Italy</div>
      <div class="brand-rule"></div>
    </div>
    <p class="front-web">www.lorvanti.com</p>
  </section>

  <section class="card card-back" aria-label="Card back">
    <div class="back-mark"><span class="back-mark-name">LORVANTI</span></div>
    <div class="divider"></div>
    <div class="contact">
      <p class="contact-name">Dario Lorvanti</p>
      <p class="contact-title">CEO &amp; CO Founder</p>
      <p class="contact-address">4817 E Halvern</p>
      <ul class="contact-list">
        <li><svg viewBox="0 0 12 12"><path d="M2 1h2l1 3-1.5 1a6 6 0 0 0 3.5 3.5L8 7l3 1v2a1 1 0 0 1-1 1A9 9 0 0 1 1 2a1 1 0 0 1 1-1z"/></svg>555-384-1926</li>
        <li><svg viewBox="0 0 12 12"><rect x="3" y="1" width="6" height="3"/><rect x="1" y="4" width="10" height="5" rx="1"/><rect x="3" y="8" width="6" height="3"/></svg>555-384-1926</li>
        <li><svg viewBox="0 0 12 12"><path d="M1 2.5h10v7H1z M1 2.5l5 4 5-4" fill="none" stroke="#d9ad3c" stroke-width="1.4"/></svg>dario@lorvanti.com</li>
        <li><svg viewBox="0 0 12 12"><circle cx="6" cy="6" r="5"/></svg>LORVANTI.COM</li>
      </ul>
    </div>
  </section>
</main>
</body>
</html>
```